TALMORK

The business want a professional looking business card. We have a scetch we will add but want the extra upgrade, and would like more suggestions for variations of our business cards.

```html
<!DOCTYPE html>
<html lang="en">
<head>
<meta charset="UTF-8">
<title>TALMORK — Business Card</title>
<link rel="stylesheet" href="https://fonts.googleapis.com/css2?family=Playfair+Display:wght@600;700&family=Montserrat:wght@400;500&display=swap">
<style>
  :root {
    --backdrop: #2b2b2b;
    --card-black: #121212;
    --pattern-grey: #3a3a3a;
    --gold: #d2a640;
    --gold-deep: #a87d22;
    --text-light: #f2f2f2;
  }
  * { margin: 0; padding: 0; box-sizing: border-box; }
  html, body {
    width: 1200px; height: 875px; overflow: hidden;
    background: var(--backdrop);
  }
  .canvas {
    width: 1200px; height: 875px;
    display: flex; flex-direction: column;
    align-items: center; justify-content: center; gap: 48px;
  }
  .card {
    position: relative;
    width: 620px; height: 354px;
    background: var(--card-black);
    border-radius: 22px;
    border: 2px solid var(--gold);
    overflow: hidden;
    box-shadow: 0 14px 30px rgba(0,0,0,0.45);
  }

  /* Front */
  .card-front .pattern-field {
    position: absolute; inset: 0;
    background: linear-gradient(100deg, var(--pattern-grey) 0%, #2a2a2a 38%, var(--card-black) 62%);
  }
  .brand-lockup {
    position: absolute;
    display: flex; flex-direction: column; align-items: center;
  }
  .card-front .brand-lockup { left: 0; right: 0; top: 50%; transform: translateY(-50%); }
  .brand-mark-dot {
    width: 34px; height: 34px; border-radius: 50%;
    background: var(--gold); margin-bottom: 18px;
  }
  .brand-name {
    font-family: 'Playfair Display', serif;
    font-weight: 600;
    color: var(--gold);
    letter-spacing: 0.04em;
    line-height: 1;
  }
  .card-front .brand-name { font-size: 58px; }
  .brand-tagline {
    font-family: 'Playfair Display', serif;
    font-weight: 600;
    color: var(--gold);
    letter-spacing: 0.5em;
    margin-top: 12px;
  }
  .card-front .brand-tagline { font-size: 15px; }

  /* Back */
  .card-back .brand-lockup { left: 40px; width: 230px; top: 50%; transform: translateY(-50%); }
  .card-back .brand-mark-dot { width: 26px; height: 26px; margin-bottom: 14px; }
  .card-back .brand-name { font-size: 40px; }
  .card-back .brand-tagline { font-size: 11px; margin-top: 9px; }
  .divider {
    position: absolute; left: 292px; top: 92px;
    width: 1.5px; height: 170px;
    background: var(--gold);
  }
  .contact-block {
    position: absolute; left: 322px; top: 92px; right: 20px;
  }
  .person-name {
    font-family: 'Playfair Display', serif;
    font-weight: 700;
    font-size: 27px;
    color: var(--gold);
    line-height: 1.1;
  }
  .person-role {
    font-family: 'Montserrat', sans-serif;
    font-weight: 500;
    font-size: 14px;
    color: var(--text-light);
    margin-top: 6px;
  }
  .contact-list { list-style: none; margin-top: 22px; }
  .contact-item {
    display: flex; align-items: center; gap: 10px;
    font-family: 'Montserrat', sans-serif;
    font-size: 14px;
    color: var(--text-light);
    margin-bottom: 9px;
  }
  .contact-icon { width: 14px; height: 14px; flex: none; fill: var(--gold); }
</style>
</head>
<body>
<main class="canvas">

  <section class="card card-front" aria-label="Business card front">
    <div class="pattern-field" role="img" aria-label="Repeating floral pattern fading from grey on the left into black"></div>
    <div class="brand-lockup">
      <span class="brand-mark-dot"></span>
      <span class="brand-name">TALMORK</span>
      <span class="brand-tagline">SINCE 2026</span>
    </div>
  </section>

  <section class="card card-back" aria-label="Business card back">
    <div class="brand-lockup">
      <span class="brand-mark-dot"></span>
      <span class="brand-name">TALMORK</span>
      <span class="brand-tagline">SINCE 2026</span>
    </div>
    <span class="divider"></span>
    <div class="contact-block">
      <h1 class="person-name">Anders Lykke Solvang</h1>
      <p class="person-role">CEO &amp; Founder</p>
      <ul class="contact-list">
        <li class="contact-item">
          <svg class="contact-icon" viewBox="0 0 16 16" aria-hidden="true"><path d="M3 1h3l1.5 4-2 1.2a9 9 0 0 0 4.3 4.3L11 8.5l4 1.5v3a2 2 0 0 1-2 2A13 13 0 0 1 1 3a2 2 0 0 1 2-2z"/></svg>
          004795550142
        </li>
        <li class="contact-item">
          <svg class="contact-icon" viewBox="0 0 16 16" aria-hidden="true"><path d="M1 3h14v10H1z M1 3l7 6 7-6" fill="none" stroke="#d2a640" stroke-width="1.6"/></svg>
          talmork.llc@postbox.com
        </li>
        <li class="contact-item">
          <svg class="contact-icon" viewBox="0 0 16 16" aria-hidden="true"><circle cx="8" cy="8" r="6.5" fill="none" stroke="#d2a640" stroke-width="1.5"/><path d="M1.5 8h13M8 1.5c-3 3.5-3 9.5 0 13M8 1.5c3 3.5 3 9.5 0 13" fill="none" stroke="#d2a640" stroke-width="1.2"/></svg>
          www.talmork.llc
        </li>
      </ul>
    </div>
  </section>

</main>
</body>
</html>
```